VELTRAQ - A modern gin bottle label

Design of a bottle label in a modern fresh design. The name of the gin is "VELTRAQ Comet Edition V1". Please take a look at the veltraq.de website. on the main page of veltraq.de you can breathe the design direction here: 1) the taste of the gin should be composed of 10 botanicals ... an important scent note. ) a distinctive flavor is spicy and fresh 3.) The filling volume is 0.5 liters 4.) the alcohol content is 43% vol. 5.) the variety is called "dry gin" 6.) veltraq stands for "energy" and "love"

Target Market(s)

Alcohol consumer

Colors

Designer to choose colors to be used in the design.

Requirements
Must have
• the veltraq corporate logo must be included, the name of the gin is "VELTRAQ Comet Edition V1"
Nice to have
• Please use the bottles template in the appendix. (The Black Bottles) they can use the saying "DESTILLED & BOTTLED BY OLD MARSHAL" in small letters

```html
<!DOCTYPE html>
<html lang="en">
<head>
<meta charset="UTF-8">
<title>VELTRAQ Comet Edition V1 – Label</title>
<link rel="stylesheet" href="https://fonts.googleapis.com/css2?family=Michroma&family=Metal+Mania&family=Rubik+Dirt&family=Roboto:wght@400&display=swap">
<style>
  :root {
    --backdrop: #bfe0e5;
    --label-black: #141414;
    --texture-light: #75736d;
    --texture-mid: #4d4b47;
    --texture-dark: #2a2927;
    --brand-orange: #f26a12;
    --flavour-orange: #e2550b;
    --text-white: #ecebe6;
    --text-ink: #121212;
  }
  * { margin: 0; padding: 0; box-sizing: border-box; }
  html, body {
    width: 1200px;
    height: 900px;
    overflow: hidden;
    background: var(--backdrop);
  }
  .canvas {
    position: relative;
    width: 1200px;
    height: 900px;
    display: flex;
    align-items: center;
    justify-content: center;
  }
  .label {
    position: relative;
    width: 522px;
    height: 828px;
    background: var(--label-black);
    overflow: hidden;
    border-radius: 6px;
  }
  .label-texture {
    position: absolute;
    inset: 0 0 110px 0;
    background:
      radial-gradient(ellipse at 45% 45%, var(--texture-light) 0%, var(--texture-mid) 45%, var(--texture-dark) 80%),
      var(--texture-dark);
    -webkit-mask-image: linear-gradient(to bottom, transparent 0, #000 30px, #000 82%, transparent 100%);
    mask-image: linear-gradient(to bottom, transparent 0, #000 30px, #000 82%, transparent 100%);
  }
  .label-content {
    position: relative;
    height: 100%;
    text-align: center;
  }
  .brand-mark {
    position: absolute;
    top: 70px;
    left: 0;
    right: 0;
    display: flex;
    flex-direction: column;
    align-items: center;
    gap: 12px;
  }
  .brand-mark-square {
    width: 22px;
    height: 22px;
    background: var(--brand-orange);
  }
  .brand-mark-name {
    font-family: "Michroma", sans-serif;
    font-size: 27px;
    letter-spacing: 5px;
    color: var(--text-white);
  }
  .product-title {
    position: absolute;
    top: 232px;
    left: 0;
    right: 0;
    font-family: "Metal Mania", cursive;
    font-size: 118px;
    line-height: 1;
    color: var(--brand-orange);
  }
  .edition {
    position: absolute;
    top: 382px;
    left: 0;
    right: 0;
    font-family: "Rubik Dirt", sans-serif;
    font-size: 44px;
    letter-spacing: 3px;
    color: var(--text-white);
    transform: scaleX(0.82);
  }
  .gin-style {
    position: absolute;
    top: 478px;
    left: 0;
    right: 0;
    font-family: "Rubik Dirt", sans-serif;
    font-size: 31px;
    letter-spacing: 1px;
    color: var(--text-ink);
    transform: scaleX(0.88);
  }
  .flavour {
    position: absolute;
    top: 560px;
    left: 0;
    right: 0;
    font-family: "Rubik Dirt", sans-serif;
    font-size: 27px;
    letter-spacing: 2px;
    color: var(--flavour-orange);
    transform: scaleX(0.85);
  }
  .spec-line {
    position: absolute;
    top: 712px;
    left: 0;
    right: 0;
    display: flex;
    justify-content: center;
    align-items: center;
    gap: 12px;
    font-family: "Roboto", sans-serif;
    font-size: 27px;
    color: var(--text-white);
  }
  .spec-divider {
    width: 2px;
    height: 32px;
    background: var(--text-white);
  }
</style>
</head>
<body>
  <main class="canvas">
    <article class="label">
      <div class="label-texture" role="img" aria-label="Weathered grey scratched texture behind the label text"></div>
      <div class="label-content">
        <div class="brand-mark">
          <span class="brand-mark-square"></span>
          <span class="brand-mark-name">VELTRAQ</span>
        </div>
        <h1 class="product-title">VELTRAQ</h1>
        <p class="edition">COMET EDITION V1</p>
        <p class="gin-style">FRESH N SPICY DRY GIN</p>
        <p class="flavour">ORANGE FLAVOUR</p>
        <p class="spec-line">
          <span class="spec-volume">0.5 fl oz</span>
          <span class="spec-divider"></span>
          <span class="spec-abv">43% alcohol</span>
        </p>
      </div>
    </article>
  </main>
</body>
</html>
```